Meadowlark Property Review is a leading provider of residential appraisal and home inspection products in S

I need a business card/logo designed that obviously describes my business. We are a residential appraisal and home inspection company in Springfield, MO. We offer residential appraisals, home inspection, pest inspection and radon gas measurement. We have been in business for 18 years and hold state certified residential appraisal licenses and OBREX certified home inspection licenses. I have a logo that I really like and will attach, but would be open to new suggestions. I like more modern designs than traditional and would like a two sided card with our services, licenses and qualifications on the back.

```html
<!DOCTYPE html>
<html lang="en">
<head>
<meta charset="utf-8">
<title>Meadowlark Property Review – Business Card</title>
<link href="https://fonts.googleapis.com/css2?family=Lato:wght@400;700&display=swap" rel="stylesheet">
<style>
  :root {
    --page: #2a2a2a;
    --card-white: #fbfbfb;
    --orange: #f2a23a;
    --ink: #4a4a4a;
    --ink-soft: #8a8a8a;
    --brown-light: #a77c45;
    --brown-dark: #7a5627;
    --cream: #f7efe3;
    --gold: #d8b04a;
  }
  * { box-sizing: border-box; margin: 0; padding: 0; }
  html, body { width: 1200px; height: 997px; overflow: hidden; }
  body {
    background: var(--page);
    font-family: "Lato", sans-serif;
    position: relative;
  }
  .card {
    position: absolute;
    left: 220px;
    width: 760px;
    height: 434px;
    box-shadow: 0 10px 30px rgba(0,0,0,.5);
  }
  /* ---------- front ---------- */
  .card-front { top: 50px; background: var(--card-white); }
  .brand-front {
    position: absolute; left: 60px; top: 150px;
    font-size: 30px; font-weight: 700; color: var(--orange);
    line-height: 1.1; width: 260px;
  }
  .holder { position: absolute; right: 60px; top: 50px; text-align: right; }
  .holder-name { font-size: 26px; font-weight: 700; color: var(--orange); }
  .holder-title { font-size: 17px; color: var(--ink); margin-top: 4px; }
  .divider {
    position: absolute; right: 60px; top: 130px; width: 380px;
    border-top: 2px solid var(--orange);
  }
  .web {
    position: absolute; right: 60px; top: 150px;
    font-size: 16px; letter-spacing: 5px; color: var(--ink-soft);
  }
  .address {
    position: absolute; right: 60px; top: 182px;
    font-size: 16px; color: var(--orange);
  }
  .credential {
    position: absolute; right: 60px; top: 250px;
    display: flex; flex-direction: column; align-items: flex-end; gap: 8px;
  }
  .credential-badge { width: 64px; height: 64px; border-radius: 50%; background: radial-gradient(circle, #f1d77e, var(--gold)); border: 3px solid #b58a2a; }
  .credential-text { font-size: 17px; color: var(--ink); }
  .contacts {
    position: absolute; left: 60px; bottom: 40px;
    list-style: none; display: flex; flex-direction: column; gap: 10px;
  }
  .contacts li { display: flex; align-items: center; gap: 12px; font-size: 19px; color: var(--ink); }
  .contacts svg { width: 20px; height: 20px; fill: var(--brown-light); }
  /* ---------- back ---------- */
  .card-back {
    top: 513px;
    background: linear-gradient(135deg, var(--brown-dark), var(--brown-light));
  }
  .services {
    position: absolute; left: 50px; top: 36px;
    list-style: none; display: flex; flex-direction: column; gap: 6px;
  }
  .services li { font-size: 20px; color: var(--cream); display: flex; align-items: center; gap: 14px; }
  .services li::before { content: "»"; color: var(--orange); font-weight: 700; font-size: 22px; }
  .brand-back {
    position: absolute; right: 60px; top: 110px; width: 330px;
    font-size: 34px; font-weight: 700; color: #ffffff; line-height: 1.1; text-align: center;
  }
  .tagline {
    position: absolute; right: 50px; bottom: 40px;
    font-size: 22px; letter-spacing: 4px; color: var(--cream);
    text-decoration: underline; text-underline-offset: 6px;
  }
</style>
</head>
<body>
  <section class="card card-front" aria-label="Card front">
    <div class="brand-front">Meadowlark Property Review</div>
    <div class="holder">
      <div class="holder-name">Dana Whitfield</div>
      <div class="holder-title">Project Manager/Estimator</div>
    </div>
    <div class="divider"></div>
    <div class="web">www.meadowlarkreview.com</div>
    <div class="address">480 E Larkspur Road Suite C Springfield, MO 65804</div>
    <div class="credential">
      <div class="credential-badge" role="img" aria-label="Certification badge"></div>
      <div class="credential-text">18 years Experience</div>
    </div>
    <ul class="contacts">
      <li><svg viewBox="0 0 24 24" aria-hidden="true"><path d="M6.6 10.8a15 15 0 0 0 6.6 6.6l2.2-2.2c.3-.3.7-.4 1-.2 1.1.4 2.3.6 3.6.6.6 0 1 .4 1 1V20c0 .6-.4 1-1 1A17 17 0 0 1 3 4c0-.6.4-1 1-1h3.5c.6 0 1 .4 1 1 0 1.3.2 2.5.6 3.6.1.3 0 .7-.2 1z"/></svg>417-555-0142</li>
      <li><svg viewBox="0 0 24 24" aria-hidden="true"><path d="M6 2h10v6H6zM3 9h18v9h-3v4H6v-4H3zm5 6v5h8v-5z"/></svg>417-555-0187</li>
      <li><svg viewBox="0 0 24 24" aria-hidden="true"><path d="M2 5h20v14H2zm2 2v.4l8 5.2 8-5.2V7z"/></svg>info@meadowlarkreview.com</li>
    </ul>
  </section>

  <section class="card card-back" aria-label="Card back">
    <ul class="services">
      <li>Tax Appeal</li>
      <li>Energy Audits</li>
      <li>Asset Evaluation</li>
      <li>Termite Inspection</li>
      <li>Mechanical Inspection</li>
      <li>Home Inspection</li>
      <li>Pest Inspection</li>
      <li>Residential Appraisals</li>
      <li>Property Inspection</li>
      <li>Radon Gas measurement</li>
    </ul>
    <div class="brand-back">Meadowlark Property Review</div>
    <div class="tagline">Delivers Accurate Property Analysis</div>
  </section>
</body>
</html>
```